RB Halden Electric Yard Sign

Looking to have a yard sign designed that we can place at projects we are working on. Most likely will be 18" H x 24" W but flexible that we can increase the size if necessary. It should include our logo, our phone # 609-555-0147, website rbhaldenelectric.example and slogan, built on integrity, driven by excellence. Colors should match our brand.

```html
<!DOCTYPE html>
<html lang="en">
<head>
<meta charset="UTF-8">
<title>RB Halden Electric Yard Sign</title>
<link href="https://fonts.googleapis.com/css2?family=Montserrat:wght@700;800&display=swap" rel="stylesheet">
<style>
  :root {
    --brand-red: #e31b23;
    --brand-navy: #0b336b;
    --sign-white: #ffffff;
    --backdrop: #e9ebee;
  }
  * { margin: 0; padding: 0; box-sizing: border-box; }
  html, body {
    width: 1200px;
    height: 1200px;
    overflow: hidden;
    background: var(--backdrop);
    font-family: "Montserrat", sans-serif;
  }
  .canvas {
    width: 1200px;
    height: 1200px;
    display: flex;
    align-items: center;
    justify-content: center;
  }
  .yard-sign {
    width: 1100px;
    height: 825px;
    background: var(--sign-white);
    display: flex;
    flex-direction: column;
    box-shadow: 0 6px 24px rgba(0,0,0,0.12);
  }
  .sign-brand {
    flex: 1;
    display: flex;
    flex-direction: column;
    align-items: center;
    justify-content: center;
    padding-top: 10px;
  }
  .brand-name {
    display: flex;
    align-items: center;
    gap: 22px;
    color: var(--brand-red);
    font-weight: 800;
    font-size: 92px;
    letter-spacing: 6px;
    line-height: 1;
    text-transform: uppercase;
  }
  .brand-dot {
    width: 40px;
    height: 40px;
    border-radius: 50%;
    background: var(--brand-navy);
    flex: none;
  }
  .brand-trade {
    margin-top: 26px;
    color: var(--brand-navy);
    font-weight: 800;
    font-size: 40px;
    letter-spacing: 11px;
    line-height: 1;
  }
  .brand-rule {
    margin-top: 14px;
    width: 930px;
    height: 14px;
    display: block;
  }
  .sign-slogan {
    margin-top: 44px;
    text-align: center;
    font-weight: 800;
    font-size: 68px;
    line-height: 1.1;
    text-transform: uppercase;
  }
  .slogan-lead { color: var(--brand-red); }
  .slogan-tail { color: var(--brand-navy); }
  .sign-divider {
    height: 9px;
    background: var(--brand-red);
    margin-top: 30px;
  }
  .sign-contact {
    height: 234px;
    background: var(--brand-navy);
    color: var(--sign-white);
    display: flex;
    flex-direction: column;
    align-items: center;
    justify-content: center;
  }
  .contact-phone {
    font-weight: 800;
    font-size: 118px;
    line-height: 1;
    letter-spacing: 1px;
  }
  .contact-web {
    margin-top: 18px;
    display: flex;
    align-items: center;
    gap: 18px;
    font-weight: 700;
    font-size: 32px;
    line-height: 1;
  }
  .contact-web::before,
  .contact-web::after {
    content: "";
    width: 190px;
    height: 2px;
    background: var(--sign-white);
  }
</style>
</head>
<body>
<main class="canvas">
  <section class="yard-sign">
    <div class="sign-brand">
      <div class="brand-name"><span class="brand-dot"></span>R.B. Halden</div>
      <div class="brand-trade">Electrical Contractor</div>
      <svg class="brand-rule" viewBox="0 0 930 14" preserveAspectRatio="none" aria-hidden="true">
        <polygon points="0,0 930,0 912,7 18,7" fill="var(--brand-red)"/>
        <rect x="18" y="7" width="894" height="7" fill="var(--brand-navy)"/>
      </svg>
      <div class="sign-slogan">
        <div class="slogan-lead">Built on Integrity</div>
        <div class="slogan-tail">Driven by Excellence</div>
      </div>
    </div>
    <div class="sign-divider"></div>
    <div class="sign-contact">
      <div class="contact-phone">609-555-0147</div>
      <div class="contact-web">rbhaldenelectric.example</div>
    </div>
  </section>
</main>
</body>
</html>
```